Business Card Design - Photographer

I am a landscape photographer and I require a business card design. 

I require two designs:
1)  a double sided business card
 and
b)  a single sided business card 

The single sided design can either be the same as the double sided (with just one side having all the information)....or it can be an entire new design. Its up to you.

My corporate colours are (CMYK):

Blue   69, 32, 0, 0
Grey  72,  64,  47,  31
Green  32,  2,  91,  0
Yellow   0, 19, 92, 0
Orange  0, 39, 75, 0

Colour space in final file should be in CMYK.

The details that need to be included on the card:

- Use the provided Logo
- Name: Wiktor Baranowski
- Email:   sales@vistalumeworks.com.au
- Website:    vistalumeworks.com.au
- Twitter:    twitter.com/vistalumeworks
- Facebook:   facebook.com/vistalumeworks
- Mobile  0417 539 662

Please use the attached template to design the logo to the specified size, including the marked bleed lines. I have also attached my logo in PNG (transparent background) and ai format for you to use.

The final file should be:
- Photoshop version with layers so I can edit the name/text etc. All non vector files should be high resolution at 1039 x 697 pixels at 300 dpi.

I also require a file as:
- Vector based PDF

Anyway questions please contact me.

Thank you

Industry/Entity Type

Landscape

Logo styles of interest
Pictorial/Combination Logo
Abstract Logo
Wordmark Logo
Lettermark Logo
Requirements
Must have
• The details that need to be included on the card:

- Use the provided Logo
- Name: Wiktor Baranowski
- Email: sales@vistalumeworks.com.au
- Website: vistalumeworks.com.au
- Twitter: twitter.com/vistalumeworks
- Facebook: facebook.com/vistalumeworks
- Mobile 0417 539 662

```html
<!DOCTYPE html>
<html lang="en">
<head>
<meta charset="utf-8">
<title>Vista Lume Works – Business Card</title>
<link href="https://fonts.googleapis.com/css2?family=Cinzel:wght@500&family=Open+Sans:wght@400;600&display=swap" rel="stylesheet">
<style>
  :root {
    --slate: #3b4054;
    --orange: #f4a53d;
    --blue: #3c98d4;
    --fb: #3b5998;
    --ink: #555a66;
    --paper: #ffffff;
    --backdrop: #e9e7e4;
    --rule: #c9cbd1;
  }
  * { margin: 0; padding: 0; box-sizing: border-box; }
  html, body { width: 1200px; height: 758px; overflow: hidden; }
  body {
    background: var(--backdrop);
    position: relative;
    font-family: "Open Sans", Arial, sans-serif;
    color: var(--ink);
  }
  .card {
    position: absolute;
    top: 214px;
    width: 540px;
    height: 330px;
    background: var(--paper);
    box-shadow: 0 6px 18px rgba(0,0,0,.18);
    overflow: hidden;
  }
  .card--front { left: 40px; }
  .card--back { left: 620px; }

  /* front */
  .brand {
    position: absolute;
    left: 34px;
    top: 50px;
    width: 236px;
    text-align: center;
  }
  .brand__dot {
    width: 62px; height: 62px;
    border-radius: 50%;
    background: var(--slate);
    margin: 0 auto 12px;
  }
  .brand__name {
    font-family: "Cinzel", Georgia, serif;
    font-weight: 500;
    font-size: 21px;
    line-height: 26px;
    color: var(--slate);
    letter-spacing: .5px;
    white-space: nowrap;
  }
  .brand__tagline {
    font-family: "Cinzel", Georgia, serif;
    font-size: 8.5px;
    letter-spacing: 1.6px;
    color: var(--slate);
    border-top: 1px solid var(--slate);
    margin: 3px 14px 0;
    padding-top: 2px;
  }
  .divider {
    position: absolute;
    left: 282px;
    top: 44px;
    width: 1px;
    height: 140px;
    background: var(--rule);
  }
  .holder {
    position: absolute;
    left: 296px;
    top: 40px;
    font-size: 15px;
    font-weight: 600;
    color: var(--slate);
    white-space: nowrap;
  }
  .contacts {
    position: absolute;
    left: 296px;
    top: 68px;
    list-style: none;
    font-size: 13.5px;
    line-height: 23px;
  }
  .contacts li { display: flex; align-items: center; white-space: nowrap; }
  .contacts svg { width: 10px; height: 10px; margin-right: 7px; flex: none; }
  .wave { position: absolute; left: 0; bottom: 0; width: 540px; height: 130px; }
  .address {
    position: absolute;
    left: 28px;
    bottom: 20px;
    color: #fff;
    font-size: 14px;
    letter-spacing: 1px;
    white-space: nowrap;
  }

  /* back */
  .back-mark {
    position: absolute;
    left: 0; right: 0;
    top: 70px;
    text-align: center;
  }
  .back-mark__dot {
    width: 118px; height: 118px;
    border-radius: 50%;
    background: var(--slate);
    margin: 0 auto 16px;
  }
  .back-mark__name {
    font-family: "Cinzel", Georgia, serif;
    font-weight: 500;
    font-size: 22px;
    color: var(--slate);
  }
  .back-url {
    position: absolute;
    left: 0; right: 0;
    bottom: 52px;
    text-align: center;
    font-family: "Cinzel", Georgia, serif;
    font-size: 16px;
    color: var(--slate);
    letter-spacing: 1px;
  }
</style>
</head>
<body>

<section class="card card--front" aria-label="Business card front">
  <div class="brand">
    <div class="brand__dot"></div>
    <div class="brand__name">Vista Lume Works</div>
    <div class="brand__tagline">Fine Art Photography</div>
  </div>

  <div class="divider"></div>

  <p class="holder">Wiktor Baranowski</p>
  <ul class="contacts">
    <li>
      <svg viewBox="0 0 10 10"><rect x="2.5" y="0.5" width="5" height="9" rx="1" fill="var(--ink)"/></svg>
      0417 539 662
    </li>
    <li>
      <svg viewBox="0 0 10 10"><rect x="0.5" y="2" width="9" height="6" fill="var(--ink)"/><path d="M0.5 2 L5 5.5 L9.5 2" stroke="#fff" stroke-width="0.8" fill="none"/></svg>
      sales@vistalumeworks.com.au
    </li>
    <li>
      <svg viewBox="0 0 10 10"><circle cx="5" cy="5" r="4.5" fill="var(--ink)"/></svg>
      www.vistalumeworks
    </li>
    <li>
      <svg viewBox="0 0 10 10"><rect width="10" height="10" rx="1.5" fill="var(--blue)"/></svg>
      vistalumeworks
    </li>
    <li>
      <svg viewBox="0 0 10 10"><rect width="10" height="10" rx="1.5" fill="var(--fb)"/></svg>
      vistalumeworks
    </li>
  </ul>

  <svg class="wave" viewBox="0 0 540 130" preserveAspectRatio="none">
    <path d="M0 64 C170 30 360 12 540 6 L540 18 C360 24 170 42 0 72 Z" fill="var(--orange)"/>
    <path d="M0 72 C170 42 360 24 540 18 L540 130 L0 130 Z" fill="var(--slate)"/>
  </svg>
  <p class="address">00, Complex name, state, city 0020</p>
</section>

<section class="card card--back" aria-label="Business card back">
  <div class="back-mark">
    <div class="back-mark__dot"></div>
    <div class="back-mark__name">Vista Lume Works</div>
  </div>
  <p class="back-url">www.vistalumeworks.com.au</p>
</section>

</body>
</html>
```